Kelvara Pane Works Business Card

We need a business card design that is suitable for a Glazing Business. We Specialize in Repairing broken windows and doors and are a 24hr on call service. We manufacture Shower screens, Fly screens, Wardrobe doors, Security doors and grilles + mirrors. We stock a variety of mesh including Standard mesh, Pet resistant mesh, Tressmet & Clearweft. We would like to use a combination of Light Blue, Dark Blue, Black & White with perhaps a picture of glass breaking.

Industry/Entity Type

Business

Contact Information for Business Card

Narooma Glass Service60B Glasshouse Rocks RdNarooma NSW 2546PH / FAX - 02 44765210MOB - 0419682350 Andrewemail - kelvarapane@fenmail.example

Font styles to use
Serif

Colors
34a7d8
0255a3
ffffff

Requirements
Must have
• logo with picture of broken or cracked glass

```html
<!DOCTYPE html>
<html lang="en">
<head>
<meta charset="utf-8">
<title>Kelvara Pane Works Business Card</title>
<link href="https://fonts.googleapis.com/css2?family=Open+Sans:wght@400;600;700&display=swap" rel="stylesheet">
<style>
  :root {
    --backdrop: #3a3a3c;
    --card: #111113;
    --card-edge: #1c1c1f;
    --blue-dark: #0255a3;
    --blue-bright: #1f6fe0;
    --blue-light: #34a7d8;
    --white: #ffffff;
    --muted: #e6e6e6;
    --divider: #2a2a2e;
  }
  * { box-sizing: border-box; margin: 0; padding: 0; }
  html, body {
    width: 1200px; height: 900px; overflow: hidden;
    background: var(--backdrop);
    font-family: "Open Sans", sans-serif;
  }
  .stage {
    position: relative; width: 1200px; height: 900px;
    display: flex; align-items: center; justify-content: center; gap: 40px;
  }
  .card {
    position: relative; width: 540px; height: 310px;
    background: var(--card); border-radius: 22px;
    border: 1px solid var(--card-edge);
    box-shadow: 0 14px 30px rgba(0,0,0,.45);
    color: var(--white);
  }

  /* Contact side */
  .brand-block {
    position: absolute; left: 40px; top: 50%; transform: translateY(-50%);
    width: 190px; display: flex; flex-direction: column; align-items: center; gap: 14px;
  }
  .brand-square { width: 92px; height: 92px; background: var(--blue-light); }
  .brand-name {
    color: var(--blue-light); font-weight: 700; font-size: 17px;
    line-height: 1.2; text-align: center; text-transform: uppercase; letter-spacing: 1px;
  }
  .divider {
    position: absolute; left: 262px; top: 38px; bottom: 118px;
    width: 1px; background: var(--divider);
  }
  .contact { position: absolute; left: 290px; top: 60px; }
  .contact-name { color: var(--blue-bright); font-weight: 700; font-size: 17px; margin-bottom: 10px; }
  .contact-address { font-size: 13px; line-height: 1.45; color: var(--muted); margin-bottom: 14px; }
  .contact-list { list-style: none; font-size: 13.5px; color: var(--muted); }
  .contact-list li { display: flex; align-items: center; gap: 10px; line-height: 1.5; }
  .contact-list svg { width: 12px; height: 12px; fill: var(--blue-bright); flex: none; }

  /* Services side */
  .services {
    position: absolute; right: 46px; top: 56px; list-style: none;
    font-size: 12.5px; color: var(--muted); line-height: 1.55;
  }
  .services li { display: flex; align-items: center; gap: 9px; }
  .services li::before {
    content: ""; width: 6px; height: 6px; border-radius: 50%; background: var(--blue-bright);
  }
  .wordmark {
    position: absolute; left: 68px; top: 118px;
    display: flex; flex-direction: column; align-items: flex-start; gap: 8px;
  }
  .wordmark-square { width: 48px; height: 48px; background: var(--blue-light); margin-left: 70px; }
  .wordmark-name {
    color: var(--blue-bright); font-weight: 400; font-size: 30px; line-height: 1.1;
    text-transform: uppercase; letter-spacing: 3px;
  }
</style>
</head>
<body>
<main class="stage">
  <section class="card card--contact">
    <div class="brand-block">
      <div class="brand-square"></div>
      <div class="brand-name">Kelvara<br>Pane Works</div>
    </div>
    <div class="divider"></div>
    <div class="contact">
      <p class="contact-name">Malcolm</p>
      <p class="contact-address">17C Tindale Ridge Rd<br>Tindale NSW 2587</p>
      <ul class="contact-list">
        <li><svg viewBox="0 0 24 24"><path d="M6.6 10.8a15 15 0 0 0 6.6 6.6l2.2-2.2a1 1 0 0 1 1-.25 11.4 11.4 0 0 0 3.6.57 1 1 0 0 1 1 1V20a1 1 0 0 1-1 1A17 17 0 0 1 3 4a1 1 0 0 1 1-1h3.5a1 1 0 0 1 1 1c0 1.25.2 2.45.57 3.57a1 1 0 0 1-.25 1z"/></svg>02 48931067</li>
        <li><svg viewBox="0 0 24 24"><path d="M6 2h10v6H6zM3 9h18v11H3zm3 3v2h3v-2zm5 0v2h3v-2zm-5 4v2h3v-2zm5 0v2h3v-2z"/></svg>02 48931067</li>
        <li><svg viewBox="0 0 24 24"><path d="M7 1h10a2 2 0 0 1 2 2v18a2 2 0 0 1-2 2H7a2 2 0 0 1-2-2V3a2 2 0 0 1 2-2zm0 3v15h10V4z"/></svg>0419682350</li>
        <li><svg viewBox="0 0 24 24"><path d="M2 5h20v14H2zm2 2v.5l8 5 8-5V7z"/></svg>kelvarapane@fenmail.example</li>
      </ul>
    </div>
  </section>

  <section class="card card--services">
    <ul class="services">
      <li>Shower screens</li>
      <li>Fly screens</li>
      <li>Wardrobe doors</li>
      <li>Security doors</li>
      <li>Grilles + mirrors</li>
    </ul>
    <div class="wordmark">
      <div class="wordmark-square"></div>
      <div class="wordmark-name">Kelvara<br>Pane Works</div>
    </div>
  </section>
</main>
</body>
</html>
```